Corporate Business Card

Very professional, Modern, Not to busy, include phone address email, website
(253) 617-4930, 18761 52nd Avenue S, Kent, WA 98047, martin@plumlinegroup.com, varkoworks.com

Target Market(s)

Manufacturing

Industry/Entity Type

Aero, machining, manufacturing, Off road racing

Contact Information for Business Card

Phone, address email, website

```html
<!DOCTYPE html>
<html lang="en">
<head>
<meta charset="utf-8">
<title>Varko Works – Business Card</title>
<link rel="stylesheet" href="https://fonts.googleapis.com/css2?family=Orbitron:wght@700&family=Roboto:wght@400&display=swap">
<style>
  :root {
    --backdrop: #2a2a2a;
    --navy: #2a3866;
    --navy-deep: #243159;
    --red: #bb2025;
    --white: #f2f2f2;
    --line: #e8e8e8;
  }
  * { box-sizing: border-box; margin: 0; padding: 0; }
  html, body { width: 1200px; height: 1138px; overflow: hidden; }
  body { background: var(--backdrop); position: relative; font-family: "Roboto", sans-serif; }

  .card {
    position: absolute;
    border-radius: 16px;
    overflow: hidden;
    background: var(--navy);
  }
  .card--back { left: 274px; top: 186px; width: 623px; height: 376px; }
  .card--front { left: 276px; top: 608px; width: 618px; height: 374px; }

  .pattern-field {
    position: absolute; inset: 0;
    background: linear-gradient(180deg, #2c3a6a 0%, var(--navy-deep) 100%);
  }

  .wordmark {
    position: absolute;
    font-family: "Orbitron", sans-serif;
    font-weight: 700;
    color: var(--white);
    line-height: 1;
    white-space: nowrap;
  }
  .card--back .wordmark { left: 54px; top: 294px; font-size: 23px; }
  .wordmark-rule {
    position: absolute; height: 2px; background: var(--line);
  }
  .card--back .wordmark-rule { left: 52px; top: 334px; width: 216px; }

  .front-art { position: absolute; inset: 0; }
  .card--front .wordmark { left: 34px; top: 174px; font-size: 25px; }
  .card--front .wordmark-rule { left: 32px; top: 214px; width: 234px; }

  .contact { position: absolute; left: 336px; top: 106px; color: var(--white); }
  .contact-name {
    font-family: "Orbitron", sans-serif;
    font-weight: 700;
    font-size: 22px;
    letter-spacing: 0.5px;
    margin-bottom: 14px;
  }
  .contact-list { list-style: none; font-size: 16px; line-height: 24.5px; }
  .contact-list li { display: flex; align-items: flex-start; }
  .contact-list svg { width: 14px; height: 14px; margin: 5px 18px 0 0; flex: none; fill: var(--red); }
  .contact-list .spacer { width: 14px; margin-right: 18px; flex: none; }
</style>
</head>
<body>

<section class="card card--back" aria-label="Card back">
  <div class="pattern-field" role="img" aria-label="Embossed repeating brand-name pattern in tonal navy"></div>
  <div class="wordmark">VARKO WORKS</div>
  <div class="wordmark-rule"></div>
</section>

<section class="card card--front" aria-label="Card front">
  <svg class="front-art" width="618" height="374" viewBox="0 0 618 374">
    <path d="M0 0 H258 Q344 187 264 374 H0 Z" fill="#f0f0f0"/>
    <path d="M0 0 H252 Q332 187 250 374 H0 Z" fill="#bb2025"/>
  </svg>
  <div class="wordmark">VARKO WORKS</div>
  <div class="wordmark-rule"></div>

  <div class="contact">
    <div class="contact-name">MARTIN HALE</div>
    <ul class="contact-list">
      <li>
        <svg viewBox="0 0 24 24"><path d="M6.6 10.8a15 15 0 0 0 6.6 6.6l2.2-2.2a1 1 0 0 1 1-.25 11.4 11.4 0 0 0 3.6.57 1 1 0 0 1 1 1V20a1 1 0 0 1-1 1A17 17 0 0 1 3 4a1 1 0 0 1 1-1h3.5a1 1 0 0 1 1 1c0 1.25.2 2.45.57 3.6a1 1 0 0 1-.25 1z"/></svg>
        (253) 617-4930
      </li>
      <li>
        <svg viewBox="0 0 24 24"><path d="M2 5h20v14H2z M3 6l9 7 9-7" fill="#bb2025" stroke="#2a3866" stroke-width="1.5"/></svg>
        martin@plumlinegroup.com
      </li>
      <li>
        <svg viewBox="0 0 24 24"><path d="M12 2a7 7 0 0 0-7 7c0 5 7 13 7 13s7-8 7-13a7 7 0 0 0-7-7zm0 9.5A2.5 2.5 0 1 1 12 6.5a2.5 2.5 0 0 1 0 5z"/></svg>
        18761 52nd Avenue S,
      </li>
      <li><span class="spacer"></span>Kent, WA 98047</li>
      <li>
        <svg viewBox="0 0 24 24"><circle cx="12" cy="12" r="10"/><path d="M2 12h20M12 2c3 3 3 17 0 20M12 2c-3 3-3 17 0 20M4 7h16M4 17h16" stroke="#2a3866" stroke-width="1.2" fill="none"/></svg>
        www.varkoworks.com
      </li>
    </ul>
  </div>
</section>

</body>
</html>
```